Business Card For Halvenmoor Financial Consulting

Hi, I would like a business card designed. Bold, modern.
Please use the same design as the logo. I have also attached the website design to see the overall theme.
Wordmark Font
Color: Hex: #01AEF7

```html
<!DOCTYPE html>
<html lang="en">
<head>
<meta charset="utf-8">
<title>Halvenmoor Consulting — Business Card</title>
<link href="https://fonts.googleapis.com/css2?family=Montserrat:wght@400;500;700&display=swap" rel="stylesheet">
<style>
  :root {
    --backdrop: #d6d6d4;
    --card-white: #ffffff;
    --brand-navy: #0b3f68;
    --brand-blue: #3aabe2;
    --card-blue: #3aa9e0;
    --text-dark: #1c1c1c;
    --edge: #0b3f68;
  }
  * { box-sizing: border-box; margin: 0; padding: 0; }
  html, body {
    width: 1200px; height: 801px; overflow: hidden;
    background: var(--backdrop);
    font-family: "Montserrat", sans-serif;
  }
  .stage {
    width: 1200px; height: 801px;
    display: flex; align-items: center; justify-content: center; gap: 50px;
  }
  .card {
    width: 525px; height: 300px;
    position: relative;
    border-bottom: 3px solid var(--edge);
    box-shadow: 0 14px 30px rgba(0,0,0,0.22);
  }
  .card--front { background: var(--card-white); padding: 44px 40px; }
  .card--back { background: var(--card-blue); display: flex; align-items: center; justify-content: center; }

  .brand { display: flex; align-items: center; gap: 14px; }
  .brand__square { width: 34px; height: 34px; background: var(--brand-blue); flex: none; }
  .brand__name {
    font-weight: 700; font-size: 30px; letter-spacing: 1px;
    color: var(--brand-navy); text-transform: uppercase; line-height: 1.05;
  }
  .brand__name small { display: block; font-size: 13px; letter-spacing: 9px; }

  .person { margin: 22px 0 0 48px; }
  .person__name { font-weight: 700; font-size: 20px; color: var(--brand-blue); text-transform: uppercase; letter-spacing: .5px; }
  .person__title { font-size: 14px; color: var(--text-dark); margin-top: 2px; }

  .contacts { list-style: none; margin: 16px 0 0 48px; }
  .contacts li { display: flex; align-items: center; gap: 8px; font-size: 13px; color: var(--text-dark); line-height: 1.55; }
  .contacts svg { width: 12px; height: 12px; fill: var(--brand-blue); flex: none; }

  .address { margin: 14px 0 0 48px; font-size: 13px; line-height: 1.5; color: var(--text-dark); font-style: normal; }

  .back-brand {
    font-weight: 700; font-size: 38px; letter-spacing: 2px; text-transform: uppercase;
    color: #2f8fc4; text-align: center; line-height: 1.1;
  }
  .back-brand small { display: block; font-size: 16px; letter-spacing: 14px; margin-top: 6px; }
</style>
</head>
<body>
<main class="stage">
  <section class="card card--front" aria-label="Front of business card">
    <div class="brand">
      <span class="brand__square" aria-hidden="true"></span>
      <p class="brand__name">Halvenmoor<small>Consulting</small></p>
    </div>
    <div class="person">
      <p class="person__name">Elliot Marsh</p>
      <p class="person__title">Managing Director</p>
    </div>
    <ul class="contacts">
      <li><svg viewBox="0 0 24 24" aria-hidden="true"><path d="M6.6 10.8a15 15 0 0 0 6.6 6.6l2.2-2.2a1 1 0 0 1 1-.25 11.4 11.4 0 0 0 3.6.57 1 1 0 0 1 1 1V20a1 1 0 0 1-1 1A17 17 0 0 1 3 4a1 1 0 0 1 1-1h3.5a1 1 0 0 1 1 1c0 1.25.2 2.45.57 3.57a1 1 0 0 1-.25 1z"/></svg>123 456 789</li>
      <li><svg viewBox="0 0 24 24" aria-hidden="true"><path d="M2 5h20v14H2z M2 5l10 8 10-8" /></svg>info@yourgmail.com</li>
      <li><svg viewBox="0 0 24 24" aria-hidden="true"><circle cx="12" cy="12" r="10"/></svg>www.yourwebsite.com</li>
    </ul>
    <address class="address">Your address, City<br>State, Zip 1234</address>
  </section>

  <section class="card card--back" aria-label="Back of business card">
    <p class="back-brand">Halvenmoor<small>Consulting</small></p>
  </section>
</main>
</body>
</html>
```